Business Card for a Jewellery Brand

Business card for an upscale jewellery brand. Attached is the brand logo and icon and color board. I am looking for two card versions: one for the founder and one is generic. The card should be elegant and convey upscale and premium feel. I am open to both square and rectangle card shapes.

Industry/Entity Type

Jewelry

Contact Information for Business Card

Two cards: (1) Sunela Parvaniya (Founder) (2) General
(1) Sunela Parvaniya card should have Name: Sunela Parvaniya, Title: Founder Email id: sunela@quiremo.com.au. Phone no: +61452913307
(2) Generic card should have Email id: info@quiremo.com.au. Phone no: +61436207518

Requirements
Must have
• Workmark
• ICON
• Phone no
• Email ID
• ABN: 58219740312 (Note: ABN is Business number in Australia)
• Website: www.quiremo.com.au
• Instagram: quiremo_jewellery
• Facebook: @quiremojewellery
Nice to have
• Tagline

```html
<!DOCTYPE html>
<html lang="en">
<head>
<meta charset="utf-8">
<title>Quiremo Business Cards</title>
<link rel="stylesheet" href="https://fonts.googleapis.com/css2?family=Raleway:wght@400;500;600&family=Josefin+Sans:wght@400&display=swap">
<style>
  :root {
    --page: #ffffff;
    --card: #ffffff;
    --marble-light: #f5f7f8;
    --marble-mid: #e7ebed;
    --rose-gold: #c98a6e;
    --blush: #e38f88;
    --muted: #9a9a9a;
    --rule: #d9826f;
  }
  * { margin: 0; padding: 0; box-sizing: border-box; }
  html, body {
    width: 1200px;
    height: 738px;
    overflow: hidden;
    background: var(--page);
    font-family: "Raleway", sans-serif;
  }
  .canvas {
    position: relative;
    width: 1200px;
    height: 738px;
  }
  .card {
    position: absolute;
    top: 138px;
    width: 465px;
    height: 462px;
    background: var(--card);
    box-shadow: 0 6px 16px rgba(0, 0, 0, 0.12);
    overflow: hidden;
  }
  .card--back { left: 92px; }
  .card--front { left: 643px; }

  /* Back side */
  .marble {
    position: absolute;
    inset: 0;
    background: linear-gradient(135deg, var(--marble-light) 0%, var(--marble-mid) 55%, var(--marble-light) 100%);
  }
  .back-mark {
    position: absolute;
    left: 0;
    right: 0;
    top: 198px;
    text-align: center;
    font-family: "Josefin Sans", sans-serif;
    font-weight: 400;
    font-size: 44px;
    line-height: 1;
    letter-spacing: 8px;
    padding-left: 8px;
    color: var(--rose-gold);
  }
  .socials {
    position: absolute;
    top: 450px;
    left: 0;
    right: 0;
    transform: translateY(-50%);
    display: flex;
    justify-content: center;
    gap: 30px;
  }
  .social {
    display: flex;
    align-items: center;
    gap: 8px;
    font-size: 17px;
    line-height: 1;
    color: var(--blush);
    white-space: nowrap;
  }
  .social__badge {
    width: 24px;
    height: 24px;
    border: 2.5px solid var(--blush);
    border-radius: 5px;
    flex: none;
  }

  /* Front side */
  .wordmark {
    position: absolute;
    left: 0;
    right: 0;
    top: 92px;
    text-align: center;
    font-family: "Josefin Sans", sans-serif;
    font-weight: 400;
    font-size: 56px;
    letter-spacing: 12px;
    padding-left: 12px;
    color: var(--rose-gold);
    line-height: 1;
  }
  .person {
    position: absolute;
    left: 0;
    right: 0;
    top: 212px;
    text-align: center;
  }
  .person__name {
    font-weight: 500;
    font-size: 28px;
    line-height: 32px;
    color: var(--blush);
  }
  .person__title {
    font-size: 21px;
    line-height: 26px;
    color: var(--muted);
  }
  .divider {
    position: absolute;
    top: 290px;
    left: 146px;
    width: 173px;
    height: 1.5px;
    background: var(--rule);
  }
  .contact {
    position: absolute;
    left: 0;
    right: 0;
    top: 318px;
    list-style: none;
    text-align: center;
    font-size: 21px;
    line-height: 27px;
    color: var(--muted);
  }
</style>
</head>
<body>
<main class="canvas">
  <section class="card card--back">
    <div class="marble" role="img" aria-label="White marble texture with soft grey veining"></div>
    <div class="back-mark">QUIREMO</div>
    <div class="socials">
      <span class="social"><span class="social__badge"></span>quiremo_jewellery</span>
      <span class="social"><span class="social__badge"></span>@quiremojewellery</span>
    </div>
  </section>

  <section class="card card--front">
    <div class="wordmark">QUIREMO</div>
    <div class="person">
      <p class="person__name">Sunela Parvaniya</p>
      <p class="person__title">Founder</p>
    </div>
    <div class="divider"></div>
    <ul class="contact">
      <li>+61452913307</li>
      <li>sunela@quiremo.com.au</li>
      <li>www.quiremo.com.au</li>
      <li>ABN: 58219740312</li>
    </ul>
  </section>
</main>
</body>
</html>
```